strength and conditioning business focused on helping people move more efficiently

I need a business card designed for a Philadelphia based company called Brsk Lft Motion (pronounced Brisk Lift). We offer fitness professional services with the idea of helping people feel better and move optimally. We do this by designing and walking through individualized programs as well as minor soft tissue work. Our perfect client would be athletes but we will be marketing to parents who have children that are active They remember their former athletic days and want to get as close as possible back to that feeling. Attached will be the official logo and logo formats. I would love for the design to communicate trustworthy and creative. I would also love for the design to be square with rounded edges.

Target Market(s)

Parents of athletic children
former athletes
athletes

Industry/Entity Type

Fitness

Contact Information for Business Card

Business: Brsk Lft Performance
Name: Coach Calvin Ashworth
Position: Strength and Conditioning Coach / Certified Personal Trainer
Contact: coach.ash@brsklft.com
Text: (555)204-7781

Font styles to use
Serif
Sans Serif

Colors
fbee38
fbee3e
0255a3
3176b5
ffffff

Requirements
Must have
• use of logo
Nice to have
• Square design
rounded edges

```html
<!DOCTYPE html>
<html lang="en">
<head>
<meta charset="utf-8">
<title>Brsk Lft Motion — Business Card</title>
<link rel="stylesheet" href="https://fonts.googleapis.com/css2?family=Open+Sans:wght@800&family=Montserrat:wght@700&family=Arimo:wght@400&display=swap">
<style>
  :root {
    --navy: #0b2a6e;
    --yellow: #f5c400;
    --white: #ffffff;
    --paper: #f7f7f5;
    --ink: #1a1a1a;
    --backdrop: #dcdcdc;
  }
  * { box-sizing: border-box; margin: 0; padding: 0; }
  html, body { width: 1200px; height: 908px; overflow: hidden; }
  body {
    background: var(--backdrop);
    display: flex;
    align-items: center;
    justify-content: center;
    gap: 80px;
  }
  .card {
    position: relative;
    width: 460px;
    height: 460px;
    border-radius: 40px;
    overflow: hidden;
    box-shadow: 0 6px 18px rgba(0,0,0,0.18);
  }

  /* Back */
  .card-back {
    background: var(--navy);
    display: flex;
    align-items: center;
    justify-content: center;
  }
  .brand {
    display: flex;
    align-items: center;
    gap: 14px;
    font-family: "Open Sans", sans-serif;
    font-weight: 800;
    white-space: nowrap;
  }
  .brand-dot {
    border-radius: 50%;
    border: 3px solid var(--yellow);
    flex: none;
  }
  .card-back .brand-name { color: var(--white); font-size: 44px; }
  .card-back .brand-dot { width: 52px; height: 52px; }

  /* Front */
  .card-front {
    background: var(--paper);
    display: flex;
    flex-direction: column;
    align-items: center;
    padding-top: 58px;
  }
  .card-front .brand-name { color: var(--navy); font-size: 36px; }
  .card-front .brand-dot { width: 42px; height: 42px; }

  .person {
    margin-top: 30px;
    text-align: center;
  }
  .person-name {
    font-family: "Montserrat", sans-serif;
    font-weight: 700;
    font-size: 24px;
    color: var(--yellow);
  }
  .person-name .surname { color: var(--navy); }
  .person-role {
    margin-top: 6px;
    font-family: "Arimo", sans-serif;
    font-size: 15px;
    line-height: 1.3;
    color: var(--ink);
  }

  .contact-icons {
    margin-top: 18px;
    display: flex;
    align-items: center;
    gap: 6px;
  }
  .divider { width: 70px; height: 1.5px; background: var(--yellow); }
  .icon { width: 26px; height: 26px; display: block; }

  .contact-list {
    margin-top: 10px;
    list-style: none;
    text-align: center;
    font-family: "Arimo", sans-serif;
    font-size: 16px;
    line-height: 1.35;
    color: var(--ink);
  }

  .swoosh {
    position: absolute;
    left: 0;
    bottom: 0;
    width: 460px;
    height: 460px;
    pointer-events: none;
  }
</style>
</head>
<body>

  <section class="card card-back" aria-label="Card back">
    <div class="brand">
      <span class="brand-dot"></span>
      <span class="brand-name">Brsk Lft Motion</span>
    </div>
  </section>

  <section class="card card-front" aria-label="Card front">
    <div class="brand">
      <span class="brand-dot"></span>
      <span class="brand-name">Brsk Lft Motion</span>
    </div>

    <div class="person">
      <p class="person-name">Coach Calvin <span class="surname">Ashworth</span></p>
      <p class="person-role">Strength and Conditioning Coach /<br>Certified Personal Trainer</p>
    </div>

    <div class="contact-icons">
      <span class="divider"></span>
      <svg class="icon" viewBox="0 0 26 26" aria-label="Phone">
        <circle cx="13" cy="13" r="13" fill="var(--navy)"/>
        <path d="M9 7.5l2.2 2.6-1.2 1.5c.8 1.7 2 2.9 3.6 3.6l1.5-1.2 2.6 2.2-1.3 1.8C12.5 17.8 8.6 14 8.2 9z" fill="var(--white)"/>
      </svg>
      <svg class="icon" viewBox="0 0 26 26" aria-label="Email">
        <circle cx="13" cy="13" r="13" fill="var(--navy)"/>
        <rect x="7" y="9" width="12" height="8.5" fill="none" stroke="var(--white)" stroke-width="1.4"/>
        <polyline points="7,9 13,14 19,9" fill="none" stroke="var(--white)" stroke-width="1.4"/>
      </svg>
      <svg class="icon" viewBox="0 0 26 26" aria-label="Website">
        <circle cx="13" cy="13" r="13" fill="var(--navy)"/>
        <circle cx="13" cy="13" r="6" fill="none" stroke="var(--white)" stroke-width="1.3"/>
        <ellipse cx="13" cy="13" rx="2.6" ry="6" fill="none" stroke="var(--white)" stroke-width="1.1"/>
        <line x1="7" y1="13" x2="19" y2="13" stroke="var(--white)" stroke-width="1.1"/>
      </svg>
      <span class="divider"></span>
    </div>

    <ul class="contact-list">
      <li>(555)204-7781</li>
      <li>coach.ash@brsklft.com</li>
      <li>www.brsklft.com</li>
    </ul>

    <svg class="swoosh" viewBox="0 0 460 460" aria-hidden="true">
      <path d="M0 440 C 200 440 380 400 460 300" fill="none" stroke="var(--yellow)" stroke-width="4"/>
      <path d="M0 452 C 210 452 400 420 460 330 L460 460 L0 460 Z" fill="var(--navy)"/>
    </svg>
  </section>

</body>
</html>
```